Lumavento business card

We need a modern business card - With our 4 colors - See web: www.lumavento.dk

I have attached logo and som old business Cards we have - Lets Make the new ones shine...:-) -

Industry/Entity Type

Business

Requirements
Must have
• the logo with lumavento only,

```html
<!DOCTYPE html>
<html lang="da">
<head>
<meta charset="utf-8">
<title>Lumavento visitkort</title>
<link href="https://fonts.googleapis.com/css2?family=Open+Sans:wght@400;600;700&display=swap" rel="stylesheet">
<style>
  :root {
    --bg: #e4e4e6;
    --card: #ffffff;
    --ink: #3a3a3a;
    --lime: #8cc63f;
    --orange: #f0892e;
    --green: #9bd14a;
    --magenta: #d9329b;
    --purple: #8a3fa6;
    --white: #ffffff;
    --pattern-light: #f1f7e8;
    --pattern-tint: #f6eef5;
  }
  * { box-sizing: border-box; margin: 0; padding: 0; }
  html, body { width: 1200px; height: 950px; overflow: hidden; }
  body {
    background: var(--bg);
    font-family: "Open Sans", Arial, sans-serif;
    color: var(--ink);
    position: relative;
  }
  .card {
    position: absolute;
    left: 250px;
    width: 700px;
    height: 400px;
    background: var(--card);
    box-shadow: 0 6px 20px rgba(0,0,0,.12);
    overflow: hidden;
  }
  .card--back { top: 55px; }
  .card--front { top: 500px; }

  .back-pattern {
    position: absolute; inset: 0;
    background: linear-gradient(135deg, var(--pattern-light), var(--white) 45%, var(--pattern-tint) 75%, var(--pattern-light));
  }
  .back-brand {
    position: absolute; inset: 0;
    display: flex; align-items: center; justify-content: center; gap: 12px;
  }
  .brand-name {
    font-weight: 600;
    color: var(--ink);
    letter-spacing: 0.18em;
    font-size: 30px;
  }
  .brand-dot {
    width: 22px; height: 22px; border-radius: 50%;
    background: var(--lime);
  }

  .gradient {
    background: linear-gradient(180deg, var(--orange) 0%, var(--green) 30%, var(--magenta) 72%, var(--purple) 100%);
  }
  .edge-strip {
    position: absolute; left: 0; top: 150px;
    width: 18px; height: 235px;
    border-radius: 0 14px 14px 0;
  }
  .front-brand {
    position: absolute; left: 40px; top: 150px; width: 270px;
    text-align: center;
  }
  .front-brand .brand-row {
    display: flex; align-items: center; justify-content: center; gap: 10px;
  }
  .front-brand .brand-name { font-size: 26px; }
  .front-brand .brand-dot { width: 18px; height: 18px; }
  .brand-rule {
    height: 2px; background: var(--lime); margin: 16px 0 10px;
  }
  .tagline { font-size: 13px; color: var(--ink); }

  .contact-panel {
    position: absolute; left: 330px; right: 0; top: 38px; height: 300px;
    border-radius: 24px 0 0 24px;
    color: var(--white);
    padding: 26px 34px;
  }
  .person-name { font-size: 24px; font-weight: 700; line-height: 1.2; }
  .person-role { font-size: 15px; margin-bottom: 12px; }
  .contact-line { font-size: 15px; line-height: 1.5; }
  .contact-list { list-style: none; margin-top: 4px; }
  .contact-list li {
    display: flex; align-items: center; gap: 12px;
    font-size: 15px; line-height: 1.6;
  }
  .contact-list svg { width: 16px; height: 16px; flex: none; fill: var(--white); }
</style>
</head>
<body>

  <section class="card card--back">
    <div class="back-pattern" role="img" aria-label="Faint repeating brand pattern in soft green and pink tones"></div>
    <div class="back-brand">
      <span class="brand-dot"></span>
      <span class="brand-name">lumavento</span>
    </div>
  </section>

  <section class="card card--front">
    <div class="edge-strip gradient"></div>

    <div class="front-brand">
      <div class="brand-row">
        <span class="brand-dot"></span>
        <span class="brand-name">lumavento</span>
      </div>
      <div class="brand-rule"></div>
      <p class="tagline">medier til unge</p>
    </div>

    <div class="contact-panel gradient">
      <h1 class="person-name">Sune Halvorsen</h1>
      <p class="person-role">Salgsdirektør</p>
      <p class="contact-line">Kastanjevej 14</p>
      <p class="contact-line">2640 Lindholt</p>
      <p class="contact-line">Tlf. +45 31 42 67 90</p>
      <ul class="contact-list">
        <li>
          <svg viewBox="0 0 16 16" aria-hidden="true"><path d="M3 1h3l1.5 4-2 1.3a9 9 0 0 0 4.2 4.2L11 8.5l4 1.5v3a2 2 0 0 1-2 2A12 12 0 0 1 1 3a2 2 0 0 1 2-2z"/></svg>
          +45 31 42 67 90
        </li>
        <li>
          <svg viewBox="0 0 16 16" aria-hidden="true"><path d="M4 1h8a1 1 0 0 1 1 1v12a1 1 0 0 1-1 1H4a1 1 0 0 1-1-1V2a1 1 0 0 1 1-1zm1 2v8h6V3zm3 9.2a.9.9 0 1 0 0 1.8.9.9 0 0 0 0-1.8z"/></svg>
          +45 52 18 73 40
        </li>
        <li>
          <svg viewBox="0 0 16 16" aria-hidden="true"><path d="M1 3h14v10H1zm1.5 1.3v.4L8 8.6l5.5-3.9v-.4zm0 2.2V11.7h11V6.5L8 10.4z"/></svg>
          sh@lumavento.dk
        </li>
        <li>
          <svg viewBox="0 0 16 16" aria-hidden="true"><path d="M8 1a7 7 0 1 0 0 14A7 7 0 0 0 8 1zm0 1.5c.8 0 1.8 1.6 2.1 4.5H5.9C6.2 4.1 7.2 2.5 8 2.5zM2.6 7h1.8c.1-1.6.5-3 1-3.9A5.5 5.5 0 0 0 2.6 7zm8.9 0h1.9a5.5 5.5 0 0 0-2.9-3.9c.5.9.9 2.3 1 3.9zM2.6 9a5.5 5.5 0 0 0 2.8 3.9c-.5-.9-.9-2.3-1-3.9zm3.3 0c.3 2.9 1.3 4.5 2.1 4.5s1.8-1.6 2.1-4.5zm5.6 0c-.1 1.6-.5 3-1 3.9A5.5 5.5 0 0 0 13.4 9z"/></svg>
          www.lumavento.dk
        </li>
      </ul>
    </div>
  </section>

</body>
</html>
```